Web Infographic for Life Insurance

We need an infographic for our insurance site based on research commissioned previously. We have a report of statistics on the cost and coverage of life insurance in 1999 vs 2019. What we're looking for is an infographic that presents these statistics in an entertaining and informative way. Site is CoverWren.com
Target Market(s)
Americans ages 30-65 interested in life insurance.
Industry/Entity Type
Insurance
Number of Pages Required
1 page
Font styles to use
Sans Serif
Decorative
Colors
85cae6
faa54b
ffffff
86cfc6
Requirements
Must have
- Long vertical infographic readable on mobile devices
Nice to have
- Footnote references
Should not have
- Extremely small text
- Any brand logos or trademarked imagery other than for coverwren

```html
<!DOCTYPE html>
<html lang="en">
<head>
<meta charset="utf-8">
<title>The cost and coverage of life insurance in 1999 vs 2019 — CoverWren</title>
<link href="https://fonts.googleapis.com/css2?family=Montserrat:wght@600;700;800&family=Open+Sans:wght@400;600;700&display=swap" rel="stylesheet">
<style>
  :root {
    --orange: #faa54b;
    --orange-deep: #f7913a;
    --sky: #85cae6;
    --teal: #86cfc6;
    --white: #ffffff;
    --ink: #111111;
    --muted: #444444;
    --paper: #f6f6f6;
    --red: #d0202e;
    --dot-blue: #1f3ff0;
    --dot-green: #2fe08a;
    --dot-light: #9fd4f5;
  }
  * { margin: 0; padding: 0; box-sizing: border-box; }
  html, body { width: 1200px; height: 3888px; overflow: hidden; }
  body {
    position: relative;
    background: var(--paper);
    font-family: "Open Sans", Arial, sans-serif;
    color: var(--ink);
  }
  .abs { position: absolute; }

  /* Hero */
  .hero-bg { position: absolute; left: 0; top: 0; }
  .brand { left: 110px; top: 36px; font: 700 26px "Montserrat", Arial, sans-serif; color: var(--white); }
  .hero-title { left: 110px; top: 232px; width: 620px; font: 700 53px/68px "Montserrat", Arial, sans-serif; letter-spacing: -0.5px; color: var(--white); white-space: nowrap; }
  .hero-lede { left: 110px; top: 456px; width: 600px; font: 400 16px/26px "Open Sans", Arial, sans-serif; color: var(--white); }
  .art { border-radius: 24px; }
  .art-home { left: 745px; top: 150px; width: 420px; height: 355px; background: linear-gradient(160deg, #e85b4f 0%, #f2c98e 55%, #8cc47a 100%); opacity: .85; }
  .art-family { left: 30px; top: 634px; width: 558px; height: 520px; background: linear-gradient(150deg, #1c8fd0 0%, #f2f2f2 55%, #f25c1e 100%); opacity: .8; }

  /* Summary */
  .summary-panel { left: 623px; top: 619px; width: 577px; height: 651px; background: var(--white); }
  .summary-title { left: 681px; top: 668px; font: 700 34px "Montserrat", Arial, sans-serif; color: var(--ink); }
  .summary-range { left: 681px; top: 714px; font: 700 54px "Montserrat", Arial, sans-serif; color: var(--sky); }
  .stat-value { width: 160px; text-align: right; font: 600 17px/24px "Open Sans", Arial, sans-serif; color: var(--ink); }
  .stat-value span, .stat-label span { display: block; color: var(--sky); font-weight: 400; }
  .stat-label { font: 600 17px/24px "Open Sans", Arial, sans-serif; color: var(--ink); }
  .branch { font: 600 13px "Open Sans", Arial, sans-serif; color: var(--ink); }

  /* Purchases */
  .purchases-title { left: 0; width: 1200px; text-align: center; color: var(--ink); font-family: "Montserrat", Arial, sans-serif; font-weight: 700; }
  .note { left: 499px; top: 1922px; width: 240px; text-align: center; font: 400 15px/26px "Open Sans", Arial, sans-serif; color: var(--red); }
  .note strong { display: block; text-decoration: underline; }
  .caption { left: 810px; top: 2014px; width: 270px; text-align: center; font: 600 15px/26px "Open Sans", Arial, sans-serif; color: var(--ink); }

  /* Two columns */
  .col-teal { left: 0; top: 2184px; width: 599px; height: 936px; background: var(--teal); }
  .col-orange { left: 599px; top: 2184px; width: 601px; height: 936px; background: var(--orange); }
  .col-heading { font: 700 34px/43px "Montserrat", Arial, sans-serif; color: var(--white); }
  .row-value { font: 700 17px "Montserrat", Arial, sans-serif; color: var(--white); }
  .row-text { font: 400 15.5px/24px "Open Sans", Arial, sans-serif; color: var(--white); width: 285px; }

  /* Reasons */
  .reasons-title { left: 0; top: 3204px; width: 1200px; text-align: center; font: 700 35px/43px "Montserrat", Arial, sans-serif; color: var(--ink); }
  .bar-pct { width: 90px; text-align: center; font: 700 17px "Montserrat", Arial, sans-serif; color: var(--orange); }
  .bar-label { width: 76px; text-align: center; font: 400 10.5px/13px "Open Sans", Arial, sans-serif; color: var(--muted); }
  .survey-note { left: 0; top: 3712px; width: 1200px; text-align: center; font: 700 21px "Montserrat", Arial, sans-serif; color: var(--orange); }

  /* Footer */
  .footer { left: 0; top: 3790px; width: 1200px; height: 98px; background: var(--teal); }
  .footer-text { left: 0; top: 3832px; width: 1200px; text-align: center; font: 400 15px "Open Sans", Arial, sans-serif; color: var(--ink); }
  .footer-code { left: 1140px; top: 3834px; font: 400 12px "Open Sans", Arial, sans-serif; color: var(--ink); }
</style>
</head>
<body>

<!-- Hero background -->
<svg class="hero-bg" width="1200" height="1300" viewBox="0 0 1200 1300" aria-hidden="true">
  <polygon points="0,0 1200,0 1200,495 996,619 623,619 623,785 0,1242" fill="var(--orange)"/>
</svg>

<div class="abs brand">coverwren</div>
<h1 class="abs hero-title">The cost and coverage<br>of life insurance in<br>1999 vs 2019</h1>
<p class="abs hero-lede">Homeowners insurance doesn't work like you might think - we've done our homework to understand the policy options and benefits out there. Start by scouting your options, or viewing our reviews.</p>
<div class="abs art art-home" role="img" aria-label="Illustration of a house under a red umbrella beside an insurance clipboard, cash and a family"></div>
<div class="abs art art-family" role="img" aria-label="Illustration of a family under a blue umbrella standing on a signed insurance policy with a pen"></div>

<!-- Summary statistics -->
<div class="abs summary-panel"></div>
<h2 class="abs summary-title">SUMMARY STATISTICS</h2>
<div class="abs summary-range">1992-1997</div>

<svg class="abs" style="left:620px;top:780px" width="580" height="500" viewBox="620 780 580 500" aria-hidden="true">
  <line x1="797" y1="895" x2="797" y2="1166" stroke="#555" stroke-width="2.5" stroke-dasharray="3 5"/>
  <g fill="var(--orange)" stroke="#777" stroke-width="2">
    <circle cx="797" cy="845" r="50"/><circle cx="797" cy="1031" r="50"/><circle cx="797" cy="1216" r="50"/>
  </g>
  <g fill="var(--orange)" stroke="var(--white)" stroke-width="2">
    <circle cx="797" cy="845" r="43"/><circle cx="797" cy="1031" r="43"/><circle cx="797" cy="1216" r="43"/>
  </g>
  <g fill="var(--white)">
    <rect x="776" y="842" width="12" height="20"/><rect x="791" y="832" width="12" height="30"/><rect x="806" y="846" width="12" height="16"/>
    <polygon points="797,812 800,820 808,820 802,825 804,833 797,828 790,833 792,825 786,820 794,820"/>
  </g>
  <g fill="none" stroke="var(--white)" stroke-width="3" stroke-linecap="round">
    <circle cx="797" cy="1031" r="20"/><path d="M797 1019 V1031 H807"/>
  </g>
  <g fill="none" stroke="var(--white)" stroke-width="3">
    <rect x="775" y="1203" width="44" height="24" rx="3" transform="rotate(-12 797 1215)"/>
    <circle cx="797" cy="1215" r="6"/>
  </g>
  <g stroke="#111" stroke-width="1.5">
    <line x1="1008" y1="1034" x2="1056" y2="1034"/><line x1="1056" y1="1034" x2="1056" y2="1105"/>
  </g>
  <circle cx="1056" cy="1034" r="5" fill="#111"/><circle cx="1056" cy="1105" r="5" fill="#111"/>
</svg>

<div class="abs stat-value" style="left:564px;top:820px">3.62 M<span>(4.91)</span></div>
<div class="abs stat-value" style="left:564px;top:1020px">2.27 M</div>
<div class="abs stat-value" style="left:564px;top:1188px">132.97 M<span>(136.41)</span></div>
<div class="abs stat-label" style="left:863px;top:820px">Type Term Premium/<span>($1000 of Face)</span></div>
<div class="abs stat-label" style="left:863px;top:1020px">Length of policy</div>
<div class="abs stat-label" style="left:863px;top:1188px">Real Amount of Policy<span>(in '000s of 1990 dollars)</span></div>
<div class="abs branch" style="left:1073px;top:1026px">Non-Smoker</div>
<div class="abs branch" style="left:1073px;top:1096px">Male</div>

<!-- Purchases -->
<h2 class="abs purchases-title" style="top:1424px;font-size:33px">Number of life insurance policy purchases</h2>
<h2 class="abs purchases-title" style="top:1492px;font-size:33px">in the United States from</h2>
<h2 class="abs purchases-title" style="top:1540px;font-size:57px">1998 to 2018 (in millions)</h2>

<svg class="abs" style="left:0;top:1660px" width="1200" height="360" viewBox="0 1660 1200 360" aria-hidden="true">
  <circle cx="260" cy="1837" r="150" fill="var(--white)" stroke="var(--orange)" stroke-width="15"/>
  <circle cx="945" cy="1837" r="150" fill="var(--white)" stroke="var(--orange)" stroke-width="15"/>
  <g fill="none" stroke="#111" stroke-width="2.5" stroke-linecap="round" stroke-linejoin="round">
    <path d="M480 1837 H432 M446 1823 L432 1837 L446 1851"/>
    <path d="M724 1837 H772 M758 1823 L772 1837 L758 1851"/>
  </g>
</svg>
<div class="abs" role="img" aria-label="Illustration of a cheerful group of friends" style="left:150px;top:1742px;width:220px;height:190px;border-radius:50%;background:radial-gradient(circle, #f6c8d4 0%, #f3e3e8 70%, #ffffff 100%)"></div>
<div class="abs" role="img" aria-label="Map of the United States with states shaded by purchases" style="left:513px;top:1772px;width:212px;height:130px;border-radius:40px 60px 30px 50px;background:linear-gradient(90deg, #f7a34a 0%, #cfcfcf 40%, #6ec9df 75%, #2b6b8a 100%);opacity:.8"></div>
<div class="abs" role="img" aria-label="Illustration of a rising growth arrow, a line chart and stacks of gold coins" style="left:860px;top:1752px;width:170px;height:170px;border-radius:20px;background:linear-gradient(150deg, #e8e8ef 0%, #f7c34a 60%, #e8752d 100%)"></div>

<div class="abs note"><strong>NOTE:</strong>The growth of the Internet has reduced term life prices by 8–15 percent.</div>
<div class="abs caption">Approximately 27.8 million life insurance policies were purchased in the United States.</div>

<!-- Two columns -->
<div class="abs col-teal"></div>
<div class="abs col-orange"></div>
<h2 class="abs col-heading" style="left:63px;top:2270px">LIFE INSURANCE BY<br>THE NUMBERS</h2>
<h2 class="abs col-heading" style="left:669px;top:2270px">STATS ABOUT THE COST<br>OF LIFE INSURANCE</h2>

<svg class="abs" style="left:0;top:2380px" width="1200" height="660" viewBox="0 2380 1200 660" aria-hidden="true">
  <g stroke="var(--white)" stroke-width="1.5">
    <line x1="121" y1="2387" x2="121" y2="3033"/>
    <line x1="726" y1="2387" x2="726" y2="3033"/>
    <line x1="121" y1="2428" x2="216" y2="2428"/>
    <line x1="121" y1="2508" x2="192" y2="2508"/>
    <line x1="121" y1="2621" x2="139" y2="2621"/>
    <line x1="121" y1="2734" x2="216" y2="2734"/>
    <line x1="121" y1="2847" x2="192" y2="2847"/>
    <line x1="121" y1="2967" x2="145" y2="2967"/>
    <line x1="726" y1="2428" x2="822" y2="2428"/>
    <line x1="726" y1="2508" x2="745" y2="2508"/>
    <line x1="726" y1="2621" x2="779" y2="2621"/>
    <line x1="726" y1="2734" x2="822" y2="2734"/>
    <line x1="726" y1="2847" x2="795" y2="2847"/>
    <line x1="726" y1="2967" x2="786" y2="2967"/>
  </g>
  <circle cx="216" cy="2428" r="5" fill="var(--dot-blue)"/>
  <circle cx="192" cy="2508" r="5" fill="var(--orange)"/>
  <circle cx="139" cy="2621" r="5" fill="var(--red)"/>
  <circle cx="216" cy="2734" r="5" fill="var(--dot-blue)"/>
  <circle cx="192" cy="2847" r="5" fill="var(--orange)"/>
  <circle cx="145" cy="2967" r="5" fill="var(--red)"/>
  <circle cx="822" cy="2428" r="5" fill="var(--dot-blue)"/>
  <circle cx="745" cy="2508" r="5" fill="var(--red)"/>
  <circle cx="779" cy="2621" r="5" fill="var(--dot-green)"/>
  <circle cx="822" cy="2734" r="5" fill="var(--dot-blue)"/>
  <circle cx="795" cy="2847" r="5" fill="var(--dot-light)"/>
  <circle cx="786" cy="2967" r="5" fill="var(--dot-green)"/>
</svg>

<div class="abs row-value" style="left:66px;top:2415px">57%</div>
<div class="abs row-text" style="left:247px;top:2415px">Percent of American adults who have life insurance‡</div>
<div class="abs row-value" style="left:66px;top:2495px">32%</div>
<div class="abs row-text" style="left:247px;top:2495px">American adults with life insurance, the percent who only have group coverage — which usually isn't enough (and is rarely portable)‡</div>
<div class="abs row-value" style="left:66px;top:2608px">11X</div>
<div class="abs row-text" style="left:247px;top:2608px">The multiples of your annual income that most financial advisors recommend you need when buying life insurance for income replacement†</div>
<div class="abs row-value" style="left:66px;top:2721px">50%</div>
<div class="abs row-text" style="left:247px;top:2721px">Life insurance policies are purchased via independent agents (like PlanSage advisors, who are not beholden to any one insurance company)</div>
<div class="abs row-value" style="left:66px;top:2834px">40%</div>
<div class="abs row-text" style="left:247px;top:2834px">Life insurance policies purchased via affiliated agents (meaning they only sell products for one insurance company)‡</div>
<div class="abs row-value" style="left:66px;top:2954px">10%</div>
<div class="abs row-text" style="left:247px;top:2954px">Policies purchased directly or through group coverage</div>

<div class="abs row-value" style="left:608px;top:2415px;width:100px;text-align:right">6X-10X</div>
<div class="abs row-text" style="left:853px;top:2415px">How much more permanent life insurance (like whole life insurance) costs vs. term life insurance†</div>
<div class="abs row-value" style="left:608px;top:2495px;width:100px;text-align:right">8%</div>
<div class="abs row-text" style="left:853px;top:2495px">Average percent increase in your insurance costs as you age, assuming your health stays the same†</div>
<div class="abs row-value" style="left:608px;top:2608px;width:100px;text-align:right">30%</div>
<div class="abs row-text" style="left:853px;top:2608px">The average cost difference between sequential health ratings (preferred vs standard, for example)†</div>
<div class="abs row-value" style="left:608px;top:2721px;width:100px;text-align:right">2X TO 3X</div>
<div class="abs row-text" style="left:853px;top:2721px">How much rates for smokers cost vs. rates for nonsmokers (but a year after you quit smoking, most companies will offer you nonsmoker rates)†</div>
<div class="abs row-value" style="left:608px;top:2834px;width:100px;text-align:right">50%</div>
<div class="abs row-text" style="left:853px;top:2834px">The average difference between the least expensive and most expensive rate for the same person across insurance companies†</div>
<div class="abs row-value" style="left:608px;top:2954px;width:100px;text-align:right">30%</div>
<div class="abs row-text" style="left:853px;top:2954px">Percent difference between premiums for men and women(with women paying nearly 30% less than men, on average)†</div>

<!-- Reasons -->
<h2 class="abs reasons-title">TOP REASONS FOR BUYING LIFE<br>INSURANCE IN THE U.S.</h2>

<svg class="abs" style="left:0;top:3300px" width="1200" height="370" viewBox="0 3300 1200 370" aria-hidden="true">
  <g fill="var(--orange)">
    <rect x="349" y="3350" width="57" height="299"/>
    <rect x="438" y="3380" width="57" height="269"/>
    <rect x="527" y="3422" width="57" height="227"/>
    <rect x="616" y="3456" width="57" height="193"/>
    <rect x="704" y="3501" width="57" height="148"/>
    <rect x="793" y="3524" width="57" height="125"/>
  </g>
  <g fill="var(--orange-deep)">
    <ellipse cx="377" cy="3350" rx="28.5" ry="8"/>
    <ellipse cx="466" cy="3380" rx="28.5" ry="8"/>
    <ellipse cx="555" cy="3422" rx="28.5" ry="8"/>
    <ellipse cx="644" cy="3456" rx="28.5" ry="8"/>
    <ellipse cx="732" cy="3501" rx="28.5" ry="8"/>
    <ellipse cx="821" cy="3524" rx="28.5" ry="8"/>
  </g>
  <g fill="var(--orange)">
    <ellipse cx="377" cy="3649" rx="28.5" ry="6"/>
    <ellipse cx="466" cy="3649" rx="28.5" ry="6"/>
    <ellipse cx="555" cy="3649" rx="28.5" ry="6"/>
    <ellipse cx="644" cy="3649" rx="28.5" ry="6"/>
    <ellipse cx="732" cy="3649" rx="28.5" ry="6"/>
    <ellipse cx="821" cy="3649" rx="28.5" ry="6"/>
  </g>
</svg>

<div class="abs bar-pct" style="left:332px;top:3310px">37%</div>
<div class="abs bar-pct" style="left:421px;top:3325px">30%</div>
<div class="abs bar-pct" style="left:510px;top:3384px">28%</div>
<div class="abs bar-pct" style="left:599px;top:3419px">27%</div>
<div class="abs bar-pct" style="left:687px;top:3461px">19%</div>
<div class="abs bar-pct" style="left:776px;top:3487px">17%</div>

<div class="abs bar-label" style="left:339px;top:3660px">Income replacement</div>
<div class="abs bar-label" style="left:428px;top:3660px">Burial/final expenses</div>
<div class="abs bar-label" style="left:517px;top:3660px">Wealth transfer</div>
<div class="abs bar-label" style="left:606px;top:3660px">Pay off mortgage</div>
<div class="abs bar-label" style="left:694px;top:3660px">Replaced a policy</div>
<div class="abs bar-label" style="left:783px;top:3660px">Tax advantaged save/invest</div>

<div class="abs survey-note">HOW MANY OPTIONS COULD BE CHOSEN IN THE SURVEY</div>

<!-- Footer -->
<div class="abs footer"></div>
<div class="abs footer-text">© Copyrights 2020. Coverwren | All Rights Reserved</div>
<div class="abs footer-code">C38</div>

</body>
</html>
```